Relaydeck Tech Company Website B2B Dev Teams Mobiron

We need a completely new website for this tech company. We offer software as a service to companies that have private Mobiron software. Our clients are developers, tech teams, and companies (B2B). We offer a way to keep Mobiron devices updated worldwide without needing a Vantora Shelf account, which suits corporate-owned single-use devices very well.
Our public is technicians (software developers), not people who use smartphones. Most clients run Relaydeck on tablets, drones, point-of-sale devices, etc.
The most used feature is the background update, which requires no user interaction. Our product helps developers keep their private enterprise applications updated. Some references of what developers like to see:
mivorin.example, taskobri.example, flowquenta.example, dravelo.example, kondrix.example
The green doesn't suit it very well. Feel free to change the logo's color (source images .ai .psd attached). The current website has only five small pages. The new one can have five at most (it can have less). The images of the "update strategies" aren't good. It can be replaced by "mock-like" images mimicking how Mobiron interacts with the user. The proportion of the tool icons isn't good. The login and signup forms can be improved a lot.
We hope for a modern website for a tech company with new colors that, at first glance, convey a sense of quality. We want the current standard for SaaS (software as a service) providers' websites.
https://www.relaydeck-app.example/
NO WORDPRESS.
We want it built using Next, Nuxt, or another good static build tool.

Target Market(s)
Mobiron Software Development
Industry/Entity Type
Software
Coding
Coded - Design and coding required
Number of Pages Required
4 page
Requirements
Must have
- We want it built using Next, Nuxt, or another good static build tool

Nice to have
- Mobiron message notification mockups instead screenshots

Should not have
- wordpress

```html
<!DOCTYPE html>
<html lang="en">
<head>
<meta charset="utf-8">
<title>Relaydeck – Mobiron Enterprise App Management</title>
<link href="https://fonts.googleapis.com/css2?family=Lato:wght@400;700;900&display=swap" rel="stylesheet">
<style>
:root{
  --blue:#1d3f9e;
  --blue-dark:#16317f;
  --yellow:#fbb614;
  --yellow-deep:#f2a100;
  --pale:#e9effb;
  --ink:#222831;
  --grey:#555b66;
  --footer:#151515;
  --white:#ffffff;
}
*{box-sizing:border-box;margin:0;padding:0}
html,body{width:1200px;height:4266px;overflow:hidden}
body{position:relative;font-family:"Lato",sans-serif;color:var(--ink);background:var(--white)}
.abs{position:absolute}
.center{text-align:center}

/* hero */
.hero-photo{left:0;top:0;width:1200px;height:800px;background:linear-gradient(120deg,#5a4a3e 0%,#3b3f48 35%,#2c3e56 60%,#1f2d44 100%)}
.hero-shade{left:0;top:0;width:1200px;height:800px;background:linear-gradient(90deg,rgba(20,20,25,.55),rgba(20,20,25,.1))}
.brand{left:75px;top:48px;font-size:54px;font-weight:900;color:var(--yellow);letter-spacing:-1px}
.nav{top:66px;left:415px;display:flex;align-items:center}
.nav a{font-size:13px;font-weight:700;color:var(--white);text-decoration:none;text-transform:uppercase;margin-right:42px}
.nav a.active{color:var(--yellow)}
.btn-nav{top:57px;height:42px;font-size:13px;font-weight:700;color:var(--white);display:flex;align-items:center;justify-content:center;text-transform:uppercase}
.btn-signup{left:851px;width:132px;background:var(--yellow-deep)}
.btn-signin{left:995px;width:132px;background:var(--blue)}
.hero-title{left:75px;top:272px;font-size:52px;line-height:58px;font-weight:700;color:var(--white)}
.hero-sub{left:75px;top:408px;font-size:26px;line-height:36px;font-weight:700;color:var(--white)}
.hero-cta{left:75px;top:510px;width:162px;height:58px;background:var(--yellow-deep);color:var(--white);font-size:17px;font-weight:700;display:flex;align-items:center;justify-content:center}
.dots{display:flex;gap:11px}
.dot{width:10px;height:10px;border-radius:50%;background:var(--white)}
.dot.on{background:var(--yellow-deep)}
.dots.grey .dot{background:#7a7f88}

/* headings */
.sec-title{left:0;width:1200px;font-size:40px;font-weight:700;color:var(--ink)}
.rule{left:530px;width:140px;height:3px;background:var(--yellow-deep)}

/* quick usage */
.step-line{top:1029px;height:5px;background:#b8bcc3}
.step{width:148px;height:148px;border-radius:50%;border:2px solid var(--yellow);display:flex;align-items:center;justify-content:center}
.step-in{width:134px;height:134px;border-radius:50%;background:var(--yellow);display:flex;align-items:center;justify-content:center}
.step-label{width:360px;font-size:31px;font-weight:700;color:var(--blue)}
.step-sub{width:360px;font-size:25px;color:var(--ink)}

/* features */
.pale{left:0;width:1200px;background:var(--pale)}
.lead{left:0;width:1200px;font-size:19px;color:var(--grey)}
.card{background:var(--white);border-radius:6px;box-shadow:0 3px 10px rgba(30,50,100,.12);text-align:center}
.feature{top:1617px;width:242px;height:295px}
.feature .ico{margin:24px auto 0;width:88px;height:88px;border-radius:50%;border:2px solid var(--yellow-deep);display:flex;align-items:center;justify-content:center}
.feature .ico.solid{background:var(--yellow-deep);border:none}
.feature h3{margin-top:16px;font-size:23px;line-height:27px;color:var(--blue);font-weight:700}
.feature p{margin:12px 14px 0;font-size:15px;line-height:23px;color:var(--grey)}
.arrow{width:30px;height:40px}

/* tools */
.tool{top:2286px;width:245px;height:164px}
.tool .mark{margin-top:40px;display:flex;align-items:center;justify-content:center;gap:10px;font-size:33px;color:#333;font-weight:400}
.tool .sq{width:38px;height:38px;background:#3a3a3a}
.tool .cap{margin-top:20px;font-size:18px;line-height:24px;color:var(--blue)}
.tool .note{font-size:12px;color:var(--grey)}

/* strategies */
.phone{top:2855px;width:330px;height:425px;border-radius:4px}
.strat-label{top:3310px;width:330px;font-size:22px;font-weight:700;color:var(--blue)}

/* cta */
.cta-photo{left:0;top:3440px;width:1200px;height:600px;background:linear-gradient(180deg,#d99a10 0%,#e5a712 40%,#caa02a 100%)}
.cta-text{left:0;top:3635px;width:1200px;font-size:43px;line-height:53px;font-weight:700;color:var(--white)}
.cta-rule{left:530px;top:3825px;width:140px;height:3px;background:var(--white)}
.cta-btn{top:3901px;height:58px;background:var(--blue);color:var(--white);font-size:18px;font-weight:700;display:flex;align-items:center;justify-content:center}

/* footer */
.footer{left:0;top:4040px;width:1200px;height:226px;background:var(--footer)}
.foot-nav{left:0;top:4096px;width:1200px;display:flex;justify-content:center;gap:52px}
.foot-nav a{font-size:21px;font-weight:700;color:var(--white);text-decoration:none}
.foot-nav a.active{color:var(--yellow-deep);text-decoration:underline;text-underline-offset:6px}
.copy{left:0;top:4145px;width:1200px;font-size:14px;color:#d8d8d8}
.social{left:0;top:4190px;width:1200px;display:flex;justify-content:center;gap:22px}
.social span{font-size:14px;font-weight:700;color:var(--white)}
</style>
</head>
<body>

<!-- HERO -->
<div class="abs hero-photo" role="img" aria-label="Developer working on a laptop with code on screen"></div>
<div class="abs hero-shade"></div>
<svg class="abs" style="left:0;top:620px" width="1200" height="180" viewBox="0 0 1200 180">
  <path d="M0,95 C250,140 430,170 650,150 C850,130 1000,70 1200,20 L1200,180 L0,180 Z" fill="#ffffff"/>
  <path d="M620,152 C840,135 1000,70 1200,20 L1200,44 C1010,95 860,150 640,160 Z" fill="#1d3f9e"/>
</svg>
<div class="abs brand">Relaydeck</div>
<nav class="abs nav">
  <a class="active" href="#">Home</a><a href="#">Features</a><a href="#">Pricing</a><a href="#">Docs</a><a href="#">Status</a>
</nav>
<div class="abs btn-nav btn-signup">Sign up free</div>
<div class="abs btn-nav btn-signin">Sign in</div>
<h1 class="abs hero-title">Mobiron Enterprise<br>App Management Made Easy</h1>
<p class="abs hero-sub">Keep your private mobiron application self-updated<br>without any third-party process.</p>
<div class="abs hero-cta">SIGN UP FREE</div>
<div class="abs dots" style="left:75px;top:632px"><i class="dot on"></i><i class="dot"></i><i class="dot"></i><i class="dot"></i></div>

<!-- QUICK USAGE -->
<h2 class="abs sec-title center" style="top:845px">Quick Usage</h2>
<div class="abs rule" style="top:914px"></div>
<div class="abs step-line" style="left:312px;width:214px"></div>
<div class="abs step-line" style="left:672px;width:214px"></div>
<div class="abs step" style="left:166px;top:957px"><div class="step-in">
  <svg width="60" height="60" viewBox="0 0 60 60"><path d="M30 8v30M18 27l12 12 12-12" stroke="#fff" stroke-width="6" fill="none" stroke-linecap="round"/><rect x="10" y="44" width="40" height="9" fill="#fff"/></svg>
</div></div>
<div class="abs step" style="left:524px;top:957px"><div class="step-in">
  <svg width="64" height="64" viewBox="0 0 64 64"><circle cx="26" cy="34" r="13" fill="none" stroke="#fff" stroke-width="8" stroke-dasharray="6 4"/><circle cx="26" cy="34" r="5" fill="#fff"/><circle cx="46" cy="20" r="8" fill="none" stroke="#fff" stroke-width="5" stroke-dasharray="4 3"/></svg>
</div></div>
<div class="abs step" style="left:887px;top:957px"><div class="step-in">
  <svg width="56" height="56" viewBox="0 0 56 56"><path d="M14 8l9 10-5 6c3 7 8 12 15 15l6-5 10 9-6 7C24 48 8 32 7 14z" fill="#fff"/></svg>
</div></div>
<div class="abs step-label center" style="left:60px;top:1114px">Download</div>
<div class="abs step-sub center" style="left:60px;top:1155px">Gravlo,Mavrik,JAR</div>
<div class="abs step-label center" style="left:418px;top:1114px">Configure</div>
<div class="abs step-sub center" style="left:418px;top:1155px">MobironManifest.xml</div>
<div class="abs step-label center" style="left:781px;top:1114px">Call</div>
<div class="abs step-sub center" style="left:781px;top:1155px">Relaydeck.start()</div>

<!-- FEATURES -->
<svg class="abs" style="left:0;top:1285px" width="1200" height="150" viewBox="0 0 1200 150">
  <path d="M0,140 C200,80 420,90 620,60 C800,30 960,10 1200,40 L1200,150 L0,150 Z" fill="#e9effb"/>
  <path d="M0,140 C200,80 420,90 620,60 C760,40 840,10 960,8 C840,22 760,58 620,72 C420,100 200,98 0,160 Z" fill="#1d3f9e"/>
</svg>
<div class="abs pale" style="top:1434px;height:560px"></div>
<h2 class="abs sec-title center" style="top:1452px">Features</h2>
<div class="abs rule" style="top:1527px"></div>
<p class="abs lead center" style="top:1554px">Things that makes your life easier</p>
<svg class="abs arrow" style="left:36px;top:1744px" viewBox="0 0 30 40"><path d="M22 6L8 20l14 14" stroke="#444" stroke-width="3" fill="none"/></svg>
<svg class="abs arrow" style="left:1134px;top:1744px" viewBox="0 0 30 40"><path d="M8 6l14 14-14 14" stroke="#1d3f9e" stroke-width="3" fill="none"/></svg>

<div class="abs card feature" style="left:75px">
  <div class="ico solid"><svg width="44" height="50" viewBox="0 0 44 50"><path d="M6 3h22l10 10v34H6z" fill="none" stroke="#fff" stroke-width="3"/><rect x="2" y="28" width="40" height="12" rx="2" fill="none" stroke="#fff" stroke-width="3"/><rect x="16" y="12" width="12" height="10" fill="none" stroke="#fff" stroke-width="3"/></svg></div>
  <h3>Host your apk</h3>
  <p>Relaydeck hosts your APK encrypted and uses renowned servers. All the traffic occurs over SSL.</p>
</div>
<div class="abs card feature" style="left:344px">
  <div class="ico"><svg width="50" height="50" viewBox="0 0 50 50" fill="none" stroke="#333" stroke-width="2"><rect x="4" y="4" width="12" height="16"/><rect x="34" y="4" width="12" height="16"/><circle cx="25" cy="26" r="7"/><rect x="4" y="32" width="12" height="14"/><rect x="30" y="36" width="16" height="10"/><path d="M16 12h18M25 33v6h5"/></svg></div>
  <h3>Devices<br>Enrollment</h3>
  <p>Simple but effective ways to install your application for the first time on your devices.</p>
</div>
<div class="abs card feature" style="left:614px">
  <div class="ico"><svg width="52" height="46" viewBox="0 0 52 46" fill="none" stroke="#333" stroke-width="2"><rect x="3" y="4" width="18" height="14"/><rect x="30" y="4" width="18" height="14"/><rect x="16" y="28" width="18" height="14"/><path d="M12 18v5h28v-5M26 23v5"/></svg></div>
  <h3>Manage Versions</h3>
  <p>Enforce the application version running on the devices. After uploading an APK.</p>
</div>
<div class="abs card feature" style="left:884px">
  <div class="ico"><svg width="50" height="50" viewBox="0 0 50 50" fill="none" stroke="#333" stroke-width="2"><circle cx="23" cy="24" r="16" stroke-dasharray="5 3"/><circle cx="23" cy="24" r="7"/><circle cx="37" cy="36" r="8" fill="#fff"/><path d="M33 36l3 3 5-6"/></svg></div>
  <h3>Track<br>Installations Info</h3>
  <p>Relaydeck will show the number of online/offline installations running.</p>
</div>

<svg class="abs" style="left:0;top:1975px" width="1200" height="140" viewBox="0 0 1200 140">
  <path d="M0,120 C180,70 400,80 620,55 C820,30 980,5 1200,30 L1200,140 L0,140 Z" fill="#ffffff"/>
  <path d="M0,112 C180,62 400,70 620,45 C780,26 880,2 1000,4 C880,14 780,46 620,65 C400,92 180,94 0,135 Z" fill="#1d3f9e"/>
</svg>

<!-- TOOLS -->
<h2 class="abs sec-title center" style="top:2160px">Tools</h2>
<div class="abs rule" style="top:2227px"></div>
<svg class="abs arrow" style="left:36px;top:2348px" viewBox="0 0 30 40"><path d="M22 6L8 20l14 14" stroke="#444" stroke-width="3" fill="none"/></svg>
<svg class="abs arrow" style="left:1134px;top:2348px" viewBox="0 0 30 40"><path d="M8 6l14 14-14 14" stroke="#1d3f9e" stroke-width="3" fill="none"/></svg>
<div class="abs card tool" style="left:75px;background:#f4f5f7;box-shadow:none">
  <div class="mark"><i class="sq"></i>Corvane</div>
  <p class="cap">Try our official<br>DLL wrapper</p>
</div>
<div class="abs card tool" style="left:344px">
  <div class="mark"><i class="sq"></i>Harbolt</div>
  <p class="cap">Try our official<br>harbolt plugin.</p>
</div>
<div class="abs card tool" style="left:613px;background:#f4f5f7;box-shadow:none">
  <div class="mark"><i class="sq"></i>Flitwing</div>
  <p class="cap">Flitwing plugin.</p>
  <p class="note">* Community.</p>
</div>
<div class="abs card tool" style="left:882px;background:#f4f5f7;box-shadow:none">
  <div class="mark" style="font-size:26px"><i class="sq"></i>Reactine Kit</div>
  <p class="cap">Reactine Kit plugin</p>
  <p class="note">* Community.</p>
</div>
<div class="abs dots grey" style="left:565px;top:2492px"><i class="dot on"></i><i class="dot"></i><i class="dot"></i><i class="dot"></i></div>

<!-- UPDATE STRATEGIES -->
<svg class="abs" style="left:0;top:2550px" width="1200" height="140" viewBox="0 0 1200 140">
  <path d="M0,125 C200,80 430,80 640,50 C830,22 1000,10 1200,35 L1200,140 L0,140 Z" fill="#e9effb"/>
  <path d="M0,125 C200,80 430,80 640,50 C790,28 880,6 1000,8 C880,20 790,50 640,68 C430,96 200,100 0,150 Z" fill="#1d3f9e"/>
</svg>
<div class="abs pale" style="top:2688px;height:770px"></div>
<h2 class="abs sec-title center" style="top:2725px">Update Strategies</h2>
<div class="abs rule" style="top:2793px"></div>
<svg class="abs arrow" style="left:36px;top:3048px" viewBox="0 0 30 40"><path d="M22 6L8 20l14 14" stroke="#444" stroke-width="3" fill="none"/></svg>
<svg class="abs arrow" style="left:1134px;top:3048px" viewBox="0 0 30 40"><path d="M8 6l14 14-14 14" stroke="#1d3f9e" stroke-width="3" fill="none"/></svg>
<div class="abs phone" style="left:75px;background:linear-gradient(160deg,#4c5a3a 0%,#6b6a55 50%,#e9c9a8 100%)" role="img" aria-label="Hand holding a phone showing an update notice in the status bar"></div>
<div class="abs phone" style="left:435px;background:linear-gradient(160deg,#3c4150 0%,#6d6f78 55%,#e9c9a8 100%)" role="img" aria-label="Hand holding a phone showing a friendly update pop-up"></div>
<div class="abs phone" style="left:796px;background:linear-gradient(160deg,#3c4150 0%,#6d6f78 55%,#e9c9a8 100%)" role="img" aria-label="Hand holding a phone showing a mandatory update pop-up"></div>
<div class="abs strat-label center" style="left:75px">STATUS BAR</div>
<div class="abs strat-label center" style="left:435px">FRIENDLY POP-UP</div>
<div class="abs strat-label center" style="left:796px">ANNOYING POP-UP</div>

<!-- CTA -->
<div class="abs cta-photo" role="img" aria-label="Warm blurred office desk scene"></div>
<svg class="abs" style="left:0;top:3425px" width="1200" height="160" viewBox="0 0 1200 160">
  <path d="M0,0 L1200,0 L1200,30 C1000,10 830,25 640,60 C430,98 200,100 0,150 Z" fill="#e9effb"/>
  <path d="M0,150 C200,100 430,98 640,60 C790,32 880,10 1000,14 C880,30 790,62 640,80 C430,112 200,118 0,170 Z" fill="#1d3f9e"/>
</svg>
<p class="abs cta-text center">Host your apk, manage and enforce versions,<br>track exceptions and installations, integrate with<br>our API, and much more!</p>
<div class="abs cta-rule"></div>
<div class="abs cta-btn" style="left:253px;width:215px">SEE ALL FEATURES</div>
<div class="abs cta-btn" style="left:495px;width:213px">SEE PRICING</div>
<div class="abs cta-btn" style="left:736px;width:215px">SIGN UP FREE</div>

<!-- FOOTER -->
<footer class="abs footer"></footer>
<nav class="abs foot-nav">
  <a class="active" href="#">HOME</a><a href="#">FEATURES</a><a href="#">PRICING</a><a href="#">DOCS</a><a href="#">STATUS</a>
</nav>
<p class="abs copy center">Copyright © 2025 &nbsp;Company Name All rights reserved.</p>
<div class="abs social"><span>Friendia</span><span>Chirpr</span><span>Snapgrid</span><span>Workmesh</span><span>Vidstream</span></div>

</body>
</html>
```